Fern Pantry needs a bottle label design

We need a bottle label design that is clean, simple and fun. The labels will be for different drink products; OAT. MILK. ALMOND MILK. SOY. We imagine our FP logo at the top, then our brand name FERN PANTRY to be positioned above the the product type OAT. MILK. ALMOND MILK. SOY etc. Underneath the product is made in new zealand. At the base is a check box (suggest using hearts) to denote vegan, planet, dairy free, and recycle friendly. At bottom is bottle size eg 1L, 380ml, 250ml. These are the 3 bottle sizes. Our logo is neon green on light grey background. Fern PAntry is white. back label info to be supplied. Sleeve is under the cap and should have a solid colour around neck. Sleeve to be on white background.

Target Market(s)

25-40 - skew female

Font styles to use
Sans Serif

Requirements
Must have
• Fp Logo and fern pantry
Red hearts against the checks: vegan, recycle, dairy free, planet claims
We are using white caps
The sleeve is going from base to under top of the neck of bottle but will not cover the made in New Zealand underneath the product type eg OAT

```html
<!DOCTYPE html>
<html lang="en">
<head>
<meta charset="utf-8">
<title>Fern Pantry – Oat Milk Label</title>
<link rel="stylesheet" href="https://fonts.googleapis.com/css2?family=Montserrat:wght@400;500;600;700&display=swap">
<style>
  :root {
    --stage: #353535;
    --label-grey: #6b6d6c;
    --label-grey-light: #737574;
    --neon-green: #1fe41f;
    --white: #ffffff;
    --milk: #ececec;
    --oat: #d49a48;
    --text-grey: #6a6a6a;
    --text-dark: #2a2a2a;
  }
  * { box-sizing: border-box; margin: 0; padding: 0; }
  html, body {
    width: 720px; height: 1200px; overflow: hidden;
    background: var(--stage);
    font-family: "Montserrat", sans-serif;
  }
  .canvas { position: relative; width: 720px; height: 1200px; }
  .label {
    position: absolute; left: 140px; top: 52px;
    width: 440px; height: 1096px;
    background: linear-gradient(180deg, var(--label-grey-light) 0%, var(--label-grey) 60%);
    box-shadow: 0 10px 24px rgba(0,0,0,0.45);
    overflow: hidden;
    text-align: center;
  }
  .brand { position: absolute; top: 108px; left: 0; right: 0; }
  .brand-mark {
    font-weight: 700; font-size: 112px; line-height: 100px;
    color: var(--neon-green); letter-spacing: 1px;
  }
  .brand-name {
    margin-top: 10px;
    font-weight: 600; font-size: 19px; letter-spacing: 6px;
    color: var(--white);
  }
  .product {
    position: absolute; top: 282px; left: 0; right: 0;
    font-weight: 600; font-size: 116px; line-height: 102px;
    color: var(--white); letter-spacing: -2px;
  }
  .hero-art {
    position: absolute; left: 0; top: 470px; width: 100%; height: 360px;
    background: linear-gradient(180deg,
      rgba(255,255,255,0) 0%,
      rgba(255,255,255,0.12) 40%,
      rgba(212,154,72,0.45) 68%,
      rgba(236,236,236,0.9) 86%,
      var(--milk) 100%);
  }
  .base {
    position: absolute; left: 0; top: 828px; width: 100%; height: 268px;
    background: linear-gradient(180deg, var(--milk), #fafafa);
  }
  .origin {
    position: absolute; top: 876px; left: 0; right: 0;
    font-weight: 500; font-size: 26px; color: var(--text-grey); letter-spacing: 0;
  }
  .claims {
    position: absolute; top: 924px; left: 0; right: 0;
    display: flex; justify-content: center; gap: 14px;
    list-style: none;
    font-weight: 500; font-size: 18px; color: var(--text-dark);
  }
  .claim { display: flex; align-items: center; gap: 3px; }
  .claim svg { width: 15px; height: 15px; }
  .volume {
    position: absolute; top: 1002px; left: 0; right: 0;
    font-weight: 500; font-size: 30px; color: var(--text-dark);
  }
</style>
</head>
<body>
<div class="canvas">
  <section class="label">
    <header class="brand">
      <div class="brand-mark">FP</div>
      <div class="brand-name">FERN PANTRY</div>
    </header>
    <h1 class="product">OAT<br>MILK</h1>
    <div class="base"></div>
    <div class="hero-art" role="img" aria-label="Oat milk pouring into a splash with golden oat grains and wheat ears"></div>
    <p class="origin">MADE IN NEW ZEALAND</p>
    <ul class="claims">
      <li class="claim"><svg viewBox="0 0 16 16"><path d="M2 9 L6 13 L14 3" fill="none" stroke="#1fe41f" stroke-width="2.4" stroke-linecap="round" stroke-linejoin="round"/></svg>Vegan</li>
      <li class="claim"><svg viewBox="0 0 16 16"><path d="M2 9 L6 13 L14 3" fill="none" stroke="#1fe41f" stroke-width="2.4" stroke-linecap="round" stroke-linejoin="round"/></svg>Dairy Free</li>
      <li class="claim"><svg viewBox="0 0 16 16"><path d="M2 9 L6 13 L14 3" fill="none" stroke="#1fe41f" stroke-width="2.4" stroke-linecap="round" stroke-linejoin="round"/></svg>Recycle</li>
    </ul>
    <p class="volume">1l</p>
  </section>
</div>
</body>
</html>
```